New Wordpress Design Project - Australian native plant nursery

I'm Seeking a wordpress website with landing page with contact details and social links, that page will link to another 4 pages. I'm happy to just add in the information once the template is set up (draft text provided on word doc).
Needing pages of information pages for:
- Nursery, what we carry and that we provide garden design services, pictures of plants and gardens
- Native flowers & what we provide, flower arrangements for weddings, special occasions, pictures
- Giftwear short blurb that we carry local artisan giftwear, pictures
- about us with history of the nursery & pictures
* Also wanting a link for e-gift cards. The link will go to an external page (square) so I don’t need to set up the website for purchases.
Social media links
Social links
https://www.facebook.com/ThePebbleHollowGarden
https://www.instagram.com/thepebblehollowgardennursery

Two local native nursery websites that I like the style of:
https://www.brimbarkstemnursery.com.au/
https://www.telvoni.com.au/

I'm using two versions of our logo, we have the smaller circle and then the other logo which is stretched out. We have used the second design for our signs at the nursery, I've asked the sign guy for a copy of the design as I don't currently have one. I have vector files of the other design.

We have wordpress set up with elemantor and hosting with godaddy, I can send you the logon details once design is confirmed.

Target Market(s)

Anyone who likes gardening, we have a pretty even spread of customers across male/female and all ages

Industry/Entity Type

Garden centre with native plants, flowers and giftwear

Coding

Coded - Design and coding required

Colors
0054AA
0677BA
7BADD7
CADEEF
E8F1F8
0094D4
00A9DD
6FCCEA
C7EBF8
E9F6FB
00AB8E
00BBA5
67D7C9
C6EFE9
E9F9F6

Requirements
Must have
• Organic/modern/minimalist design
Nice to have
• Blue/white/green, flannel flowers as per logo

```html
<!DOCTYPE html>
<html lang="en">
<head>
<meta charset="utf-8">
<title>The Pebble Hollow Garden – Native Nursery</title>
<link rel="stylesheet" href="https://fonts.googleapis.com/css2?family=Della+Respira&family=Poppins:wght@400;500;600&display=swap">
<style>
:root{
  --teal:#00ab8e;
  --teal-mid:#00bba5;
  --teal-soft:#67d7c9;
  --teal-pale:#c6efe9;
  --teal-wash:#eef8f6;
  --ink:#1f1f1f;
  --body:#444;
  --white:#fff;
  --black:#000;
}
*{margin:0;padding:0;box-sizing:border-box}
html,body{width:1200px;height:3905px;overflow:hidden}
body{font-family:"Poppins",sans-serif;color:var(--body);background:var(--white);position:relative}
a{color:inherit;text-decoration:none}
.script{font-family:"Della Respira",serif;color:var(--ink);font-weight:400}

.site-header{position:absolute;top:0;left:0;width:1200px;height:85px;background:var(--white);z-index:3}
.brand{position:absolute;left:98px;top:8px;width:172px;height:166px;border-radius:50%;background:var(--white);border:2px solid #333;display:flex;align-items:center;justify-content:center;text-align:center;font-size:17px;line-height:1.3;color:#333;z-index:4;box-shadow:0 0 0 6px var(--white)}
.nav{position:absolute;left:406px;top:30px;display:flex;gap:25px;font-size:15px;color:#222}
.nav .active{color:var(--teal);border-bottom:2px solid var(--teal);padding-bottom:3px}
.btn{display:inline-block;border:2px solid var(--teal);color:var(--teal);font-weight:600;font-size:15px;padding:12px 18px;background:var(--white);box-shadow:0 3px 6px rgba(0,0,0,.15)}
.nav-cta{position:absolute;left:981px;top:17px;padding:10px 13px}

.hero{position:absolute;top:85px;left:0;width:1200px;height:600px;background:linear-gradient(120deg,#5c3b22,#8a6a4a 45%,#6b4a2c)}
.hero-photo{position:absolute;inset:0;background:radial-gradient(circle at 30% 40%,#9a8f7a 0,#6d5a45 35%,transparent 60%)}
.hero-badge{position:absolute;left:605px;top:82px;width:460px;height:460px;border-radius:50%;background:radial-gradient(circle,#2f8f72,#1d6b55);border:5px solid var(--white);display:flex;align-items:center;justify-content:center;text-align:center}
.hero-badge h1{font-family:"Della Respira",serif;color:var(--white);font-size:64px;line-height:1.18;font-weight:400}
.hero-arrow{position:absolute;top:284px;width:34px;height:34px;border-radius:50%;background:rgba(255,255,255,.6);display:flex;align-items:center;justify-content:center}

.feature{position:absolute;left:0;width:1200px}
.feature.tinted{background:var(--teal-wash)}
.feature-media{position:absolute;width:461px;height:466px;background:linear-gradient(135deg,#5b7fa0,#6f8f4c 55%,#4a5a3a)}
.media-right{border-top-right-radius:48px;box-shadow:-9px 9px 0 var(--teal-pale)}
.media-left{border-top-left-radius:48px;box-shadow:9px 9px 0 var(--teal-pale)}
.feature-copy{position:absolute;width:500px;font-size:14.2px;line-height:31px}
.feature-copy h2{font-size:42px;margin-bottom:12px}
.feature-copy p+p{margin-top:31px}
.feature-copy .btn{margin-top:22px}
.subhead{font-size:19px;color:var(--ink);margin:-4px 0 4px}

.about{position:absolute;top:2535px;left:0;width:1200px;height:336px;background:linear-gradient(180deg,#12a98c,#0fa488);text-align:center;color:var(--white)}
.about h2{color:var(--white);font-size:44px;padding-top:50px}
.about p{width:900px;margin:12px auto 0;font-size:14.2px;line-height:31px}
.about .btn{margin-top:14px;background:transparent;color:var(--white);border-color:var(--white);box-shadow:none;padding:10px 12px}

.site-footer{position:absolute;top:3477px;left:0;width:1200px;height:428px;background:var(--black);color:var(--white)}
.footer-brand{position:absolute;left:100px;top:68px;width:180px;height:180px;border-radius:50%;border:2px solid var(--white);display:flex;align-items:center;justify-content:center;text-align:center;font-size:17px;line-height:1.3}
.socials{position:absolute;left:159px;top:290px;display:flex;gap:18px}
.socials a{width:30px;height:30px;background:var(--teal)}
.footer-col{position:absolute;top:88px;font-size:14.5px;line-height:31px}
.footer-col h3{font-size:21px;font-weight:500;margin-bottom:6px}
.contact-row{display:flex;gap:18px;align-items:flex-start;line-height:21px;margin-bottom:20px}
.contact-row svg{flex:none;margin-top:2px}
.subscribe{display:flex;margin-top:8px}
.subscribe span{width:210px;height:42px;background:var(--white)}
.subscribe b{width:42px;height:42px;background:var(--teal);display:flex;align-items:center;justify-content:center}
.footer-rule{position:absolute;left:98px;top:363px;width:1003px;border-top:1px solid #777}
.copyright{position:absolute;top:386px;width:1200px;text-align:center;font-size:14.5px}
</style>
</head>
<body>

<header class="site-header">
  <a class="brand" href="#">The<br>Pebble Hollow<br>Garden</a>
  <nav class="nav">
    <a class="active" href="#">Home</a>
    <a href="#">About Us</a>
    <a href="#">Native plants</a>
    <a href="#">Flowers</a>
    <a href="#">Giftwear</a>
    <a href="#">Nursery Now</a>
  </nav>
  <a class="btn nav-cta" href="#">Contact Us</a>
</header>

<section class="hero">
  <div class="hero-photo" role="img" aria-label="Native flower arrangement with gum nuts in a driftwood pot on a wooden table"></div>
  <div class="hero-badge"><h1>Welcome To<br>The Pebble<br>Hollow Garden</h1></div>
  <span class="hero-arrow" style="left:39px"><svg width="10" height="10" viewBox="0 0 10 10"><path d="M6.5 2 3.5 5l3 3" fill="none" stroke="#555" stroke-width="1.4"/></svg></span>
  <span class="hero-arrow" style="left:1132px"><svg width="10" height="10" viewBox="0 0 10 10"><path d="M3.5 2 6.5 5l-3 3" fill="none" stroke="#555" stroke-width="1.4"/></svg></span>
</section>

<section class="feature" style="top:685px;height:626px">
  <div class="feature-media media-left" style="left:98px;top:83px" role="img" aria-label="Nursery shed with potted native plants along a gravel path"></div>
  <div class="feature-copy" style="left:600px;top:80px">
    <h2 class="script">Native Plants</h2>
    <p>At our nursery, we provide native plants that thrive in their local environment. Native plants are essential for preserving biodiversity, and they support pollinators and other wildlife while reducing human impact on the environment. At our nursery, we offer a wide selection of native plants that provide planting and care instructions to ensure that your plants thrive once they're in the ground.</p>
    <p>In addition to selling plants, we also offer consultations and design services for those looking to incorporate native plants into their landscapes or garden. We specialise in providing high-quality native plants help beautify restore natural ecosystems promote sustainability.</p>
    <a class="btn" href="#">Read More</a>
  </div>
</section>

<section class="feature tinted" style="top:1311px;height:595px">
  <div class="feature-copy" style="left:98px;top:60px;width:520px">
    <h2 class="script">Flowers</h2>
    <p>At the nursery, we specialize in creating unique arrangements using locally sourced native Australian flowers. Our team of experienced florists are passionate about showcasing the beauty of our country's flora and fauna through unique and beautiful bespoke floral designs.Our native flower arrangements are perfect for any occasion – from weddings and corporate events to simple gifts for loved ones. The vibrant colours and textures of our native flowers can add a touch of the Australian landscape space.</p>
    <p>We believe that sustainability is important, and as such, all of our native flowers are ethically sourced. We work closely with local growers and suppliers to ensure that our flowers are both beautiful and eco-friendly.</p>
    <a class="btn" href="#">Read More</a>
  </div>
  <div class="feature-media media-right" style="left:641px;top:60px;background:radial-gradient(circle at 40% 45%,#e7c7c0,#c96a78 40%,#e9c24a 70%,#7b8a5a)" role="img" aria-label="Bunch of pink eucalyptus blossom, paper daisies and billy buttons"></div>
</section>

<section class="feature" style="top:1906px;height:629px">
  <div class="feature-media media-left" style="left:98px;top:83px;background:linear-gradient(160deg,#4e7a3a,#d07a95 50%,#3f6a2c)" role="img" aria-label="Pink kangaroo paw plants growing in the nursery"></div>
  <div class="feature-copy" style="left:600px;top:82px">
    <h2 class="script">Giftwear</h2>
    <p>We are proud to offer a wide range of unique and high-quality gifts that celebrate the natural beauty of Australia's native flora and fauna. From beautifully scented candles to stunning artworks, our gift selection is sure to please.</p>
    <p>Our giftware collection features a range of products that have been designed and crafted by local artisans and small businesses. We believe in supporting our community and showcasing the amazing talent and creativity that can be found here in Australia.In addition to our locally made products, we also stock gifts from well-known brands that share our passion for nature and sustainability.</p>
    <a class="btn" href="#">Read More</a>
  </div>
</section>

<section class="about">
  <h2 class="script">About Us</h2>
  <p>The Pebble Hollow Garden business, that has been providing plants, flowers and native giftware to the Central Coast and surrounding areas since 2001. Over this time, we have established a strong connection with the community and provided expert native advice.</p>
  <a class="btn" href="#">E-Gift Cards</a>
</section>

<section class="feature" style="top:2871px;height:606px">
  <div class="feature-copy" style="left:98px;top:118px;width:520px">
    <h2 class="script">The Nursery Now</h2>
    <p class="subhead">Since then concentrating strictly on native only</p>
    <p>The business was originally established by Elsie and Marnie, ** later departed and Tessa and Gwen.</p>
    <p>Elsie Harwood has been in the native plant industry for most of her life. She has been involved in the propagation, wholesale, retail, floral design and promotion of native plants.</p>
    <a class="btn" href="#">Read More</a>
  </div>
  <div class="feature-media media-right" style="left:639px;top:64px;background:radial-gradient(circle at 50% 45%,#e59ad0,#b85aa0 40%,#5b6a4a 80%)" role="img" aria-label="Pink native flower with raindrops on its petals"></div>
</section>

<footer class="site-footer">
  <a class="footer-brand" href="#">The<br>Pebble Hollow<br>Garden</a>
  <div class="socials">
    <a href="https://www.facebook.com/ThePebbleHollowGarden" aria-label="Facebook"></a>
    <a href="https://www.instagram.com/thepebblehollowgardennursery" aria-label="Instagram"></a>
  </div>
  <div class="footer-col" style="left:361px">
    <h3>Quick Links</h3>
    <a href="#">Home</a><br><a href="#">About Us</a><br><a href="#">Native plants</a><br><a href="#">Flowers</a><br><a href="#">Giftwear</a><br><a href="#">Nursery Now</a>
  </div>
  <div class="footer-col" style="left:537px">
    <h3>Contact Us</h3>
    <div class="contact-row"><svg width="14" height="18" viewBox="0 0 14 18"><path d="M7 0a7 7 0 0 0-7 7c0 5 7 11 7 11s7-6 7-11a7 7 0 0 0-7-7zm0 9.5A2.5 2.5 0 1 1 7 4.5a2.5 2.5 0 0 1 0 5z" fill="#fff"/></svg><span>The Pebble Hollow Garden,<br>United State.</span></div>
    <div class="contact-row"><svg width="16" height="12" viewBox="0 0 16 12"><rect width="16" height="12" fill="#fff"/><path d="M0 0l8 6 8-6" fill="none" stroke="#000" stroke-width="1.3"/></svg><span>info@thepebblehollowgarden.in</span></div>
    <div class="contact-row"><svg width="15" height="15" viewBox="0 0 15 15"><path d="M3 0l3 3.5-1.8 2a9 9 0 0 0 5.3 5.3l2-1.8L15 12l-2 3C6 14.5.5 9 0 2z" fill="#fff"/></svg><span>+1800 555 0142</span></div>
  </div>
  <div class="footer-col" style="left:847px">
    <h3>Get In Touch</h3>
    <span>Lorem ipsum dolor sit amet</span>
    <div class="subscribe"><span></span><b><svg width="16" height="16" viewBox="0 0 16 16"><path d="M15 1 1 7l6 2 2 6z" fill="#fff"/></svg></b></div>
  </div>
  <div class="footer-rule"></div>
  <p class="copyright">Copyrights@2023.The Pebble Hollow Garden.All Rights Reserved</p>
</footer>

</body>
</html>
```